Design Brief for Website Redesign

Client Name: Harbourline IT
Website: www.harbourlineit.com.au
Industry: Managed IT Services
Target Audience: Small to medium-sized businesses in Australia, requiring IT solutions, IT support, cloud services, and phone systems.

Project Overview
We are seeking a full redesign of the Harbourline IT website to modernize its look, improve usability, and enhance user experience across devices. The goal is to create a professional, clean, and user-friendly website that reflects our expertise in IT services and appeals to our business clients.

Objectives
Modern Visual Identity: Create a fresh, modern design that aligns with Harbourline IT's branding.

Improved User Experience: Simplify navigation, improve accessibility, and enhance mobile responsiveness.

Clear Calls to Action: Ensure CTAs are prominent and encourage user engagement.

Enhanced Trust & Credibility: Highlight testimonials, case studies, and industry credentials.

SEO Optimization: Ensure the site is optimized for search engines, including proper heading structures and metadata.
Design Style & Tone
Professional: Clean, modern, and polished to reflect our IT expertise.

Minimalist: Simple layouts, plenty of white space, and easy-to-read typography.

Tech-focused: Subtle tech-themed design elements that reinforce our brand as a leading IT service provider.

Colors: Use our existing brand colors, or propose a color scheme that complements the tech industry while maintaining a professional feel.

Typography: Clear, readable fonts that convey professionalism and trustworthiness.

Key Pages & Features
Home Page:

Hero section with a clear value proposition.

Highlight key services (IT support, cloud solutions, phone systems, etc.) with icons and brief descriptions.

Prominent CTAs (e.g., “Request a Quote,” “Book a Demo”).

Testimonials from satisfied clients.

Services Page:

Detailed breakdown of the services we offer (IT support, cloud services, phone systems, etc.).

Use of icons or illustrations to make the services visually engaging.

Clear CTAs to request quotes or book consultations.

About Us Page:

Information about our company history, mission, and team.

Highlight our certifications, partnerships, and industry expertise.

Case Studies/Testimonials Page:

Showcase client success stories and testimonials with visuals and brief case study summaries.

Include a trust-building section with logos of major clients or partners.

Contact Page:

Simple contact form for inquiries.

Integrated map with office location.

Social media links and phone number.

Blog/Resource Section:

Easy-to-navigate blog section for IT-related articles, tips, and industry news.

Clear categorization and tags for easy browsing.

Knowledge Base/Support Page:

Self-service area for clients to find articles, FAQs, and support guides.

Option to submit a support ticket.

Mobile Responsiveness:

Ensure the design is fully responsive, with no horizontal scrolling or misaligned content on mobile.

Functional Requirements
Fast Load Times: Optimize images, minimize unnecessary scripts, and ensure the site loads quickly on both desktop and mobile.

User-Friendly CMS: We need a CMS that is easy to update (preferably WordPress, but open to other suggestions).

SEO Best Practices: Structure the site with proper metadata, alt tags, and semantic HTML for better search engine optimization.

Security: Ensure the website follows security best practices (SSL, HTTPS).

Deliverables
Full website design (desktop and mobile versions).

Design mockups in Photoshop, Sketch, or Figma (whichever is preferred).

Working prototype (optional).

Final website files, including images and assets.

A style guide for ongoing consistency.

Industry/Entity Type

IT Managed Services

Number of Pages Required

3 page

Requirements
Must have
• EXCELLENT UX/UI

```html
<!DOCTYPE html>
<html lang="en">
<head>
<meta charset="utf-8">
<title>Harbourline IT – Reliable IT Support</title>
<link rel="stylesheet" href="https://fonts.googleapis.com/css2?family=Montserrat:wght@500;600;700;800;900&family=Mulish:wght@400;500;600;700&display=swap">
<style>
:root{
  --red:#e8213a;
  --red-dark:#c41530;
  --ink:#141414;
  --text:#333;
  --muted:#555;
  --grey-bg:#f1f1f1;
  --outline:#d9d9d9;
  --footer:#0c0c0c;
  --white:#fff;
}
*{margin:0;padding:0;box-sizing:border-box}
html,body{width:1200px;height:3459px;overflow:hidden}
body{position:relative;font-family:"Mulish",sans-serif;color:var(--text);background:var(--white)}
.abs{position:absolute}

/* header / hero */
.hero{position:absolute;left:0;top:0;width:1200px;height:654px;overflow:hidden}
.hero-photo{position:absolute;inset:0;background:
  radial-gradient(ellipse 420px 300px at 880px 300px,rgba(40,110,190,.55),transparent 70%),
  radial-gradient(ellipse 700px 260px at 300px 300px,rgba(200,110,40,.45),transparent 70%),
  radial-gradient(ellipse 500px 200px at 700px 560px,rgba(30,120,200,.45),transparent 70%),
  linear-gradient(180deg,#101a2c 0%,#1a2233 45%,#0f1c2e 100%)}
.logo-word{font-family:"Montserrat",sans-serif;font-weight:800;color:var(--red);letter-spacing:-.5px;white-space:nowrap}
.site-logo{left:150px;top:36px;font-size:36px}
.nav{left:554px;top:38px;display:flex;align-items:center}
.nav a{font-family:"Montserrat",sans-serif;font-weight:600;font-size:15.5px;color:var(--white);text-decoration:none;padding:8px 15px;border-radius:20px;margin-right:16px}
.nav a.active{background:var(--red)}
.hero-title{left:150px;top:176px;font-family:"Montserrat",sans-serif;font-size:55px;line-height:53.5px;color:var(--white);font-weight:600}
.hero-title .bold{font-weight:900}
.hero-title .red{color:var(--red);font-weight:900}
.hero-sub{left:153px;top:416px;font-size:23px;line-height:31px;color:var(--white);font-weight:600;width:420px}
.btn{display:inline-flex;align-items:center;justify-content:center;background:var(--red);color:var(--white);font-family:"Montserrat",sans-serif;font-weight:700;border-radius:30px;text-decoration:none;white-space:nowrap}
.btn-hero{height:46px;width:200px;font-size:14.5px}
.btn-sm{height:28px;width:99px;font-size:10.5px}

/* section titles */
.ghost{position:absolute;left:0;width:1200px;text-align:center;font-family:"Montserrat",sans-serif;font-weight:800;font-size:76px;letter-spacing:3px;color:transparent;-webkit-text-stroke:1.5px var(--outline);line-height:1}
.pill-title{position:absolute;height:40px;display:flex;align-items:center;justify-content:center;background:var(--red);color:var(--white);font-family:"Montserrat",sans-serif;font-weight:800;font-size:30px;border-radius:24px;white-space:nowrap}

/* services */
.services{position:absolute;left:0;top:654px;width:1200px;height:594px;background:var(--grey-bg)}
.service-card{position:absolute;top:206px;width:213px;height:316px;background:var(--white);border-radius:6px;text-align:center;border:2px solid transparent}
.service-card.featured{border-color:var(--red)}
.service-card svg{position:absolute;left:74px;top:34px}
.service-card h3{position:absolute;left:0;right:0;top:134px;font-family:"Montserrat",sans-serif;font-weight:700;font-size:15px;color:var(--ink)}
.service-card p{position:absolute;left:32px;right:32px;top:170px;font-size:12px;line-height:16.4px;color:var(--muted)}
.service-card .btn{position:absolute;left:56px;top:283px}
.arrow{position:absolute;width:35px;height:35px;border:1.5px solid #888;border-radius:50%;display:flex;align-items:center;justify-content:center}

/* welcome */
.welcome{position:absolute;left:0;top:1248px;width:1200px;height:407px;background:var(--white);overflow:hidden}
.welcome-pill{left:161px;top:51px;width:177px;height:40px;font-size:21px;border-radius:22px}
.welcome-name{left:354px;top:48px;font-size:40px}
.welcome p{position:absolute;left:360px;top:123px;width:240px;font-size:14px;line-height:20.2px;color:var(--ink)}

/* testimonials */
.testimonial{position:absolute;top:1942px;width:422px;height:208px;border:1.5px solid #cfcfcf;border-radius:6px;background:var(--white)}
.testimonial p{position:absolute;left:40px;top:44px;right:40px;font-size:12.5px;line-height:19.4px;color:var(--ink)}
.quote-mark{position:absolute;font-family:"Montserrat",sans-serif;font-weight:900;font-size:76px;color:var(--red);line-height:1;background:var(--white);padding:0 4px}
.author{position:absolute;top:2171px;display:flex;align-items:center;gap:20px}
.client-badge{display:flex;align-items:center;gap:6px;height:30px;padding:0 8px;border:1px solid #bbb;border-radius:2px;font-size:10px;font-weight:700;color:var(--ink);white-space:nowrap}
.client-badge i{width:12px;height:12px;background:#3f5a45;display:block}
.author b{display:block;font-size:13px;color:var(--ink)}
.author span{font-size:12.5px;color:var(--muted)}

/* blog */
.blog{position:absolute;left:0;top:2286px;width:1200px;height:715px;background:var(--grey-bg)}
.post{position:absolute;top:233px;width:284px}
.post-image{height:222px;border-radius:8px}
.post h3{margin-top:26px;font-family:"Montserrat",sans-serif;font-weight:700;font-size:14.8px;line-height:22px;color:var(--ink);height:66px}
.post p{margin-top:12px;font-size:13px;line-height:18px;color:var(--text);height:52px}
.post .btn{margin-top:18px}

/* footer */
.footer-rule{position:absolute;left:0;top:3000px;width:1200px;height:7px;background:var(--red)}
.footer{position:absolute;left:0;top:3007px;width:1200px;height:452px;background:var(--footer);color:var(--white)}
.footer-name{left:150px;top:96px;font-size:40px}
.footer h4{position:absolute;font-family:"Montserrat",sans-serif;font-weight:700;font-size:18px}
.footer h4::after{content:"";display:block;width:44px;height:1px;background:#aaa;margin-top:14px}
.footer ul{position:absolute;list-style:none;font-size:12.5px;line-height:22.5px;color:#ddd}
.btn-footer{position:absolute;left:844px;width:200px;height:46px;font-size:14px}
.socials{position:absolute;left:844px;top:3265px;display:flex;gap:6px}
.socials span{width:33px;height:33px;border-radius:50%;background:var(--white);display:block}
.footer-line{position:absolute;left:150px;top:343px;width:900px;height:1px;background:#333}
.copyright{position:absolute;left:0;width:1200px;top:388px;text-align:center;font-size:12.5px;color:#ddd}
</style>
</head>
<body>

<header class="hero">
  <div class="hero-photo" role="img" aria-label="Man working on a laptop above a glowing night city with a blue network overlay"></div>
  <div class="abs logo-word site-logo">harbourline</div>
  <nav class="abs nav">
    <a class="active" href="#">HOME</a><a href="#">ABOUT US</a><a href="#">SERVICES</a><a href="#">BLOG</a><a href="#">CONTACT</a>
  </nav>
  <h1 class="abs hero-title"><span class="bold">RELIABLE</span><br><span class="red">IT SUPPORT,</span><br>ANYTIME YOU<br>NEED IT</h1>
  <p class="abs hero-sub">Expert tech solutions to keep your business running smoothly.</p>
  <a class="abs btn btn-hero" style="left:153px;top:510px" href="#">REQUEST QUOTES</a>
  <a class="abs btn btn-hero" style="left:376px;top:510px;width:176px" href="#">BOOK A DEMO</a>
</header>

<section class="services">
  <div class="ghost" style="top:36px">OUR SERVICES</div>
  <h2 class="pill-title" style="left:471px;top:126px;width:256px">OUR SERVICES</h2>

  <div class="arrow" style="left:70px;top:356px"><svg width="12" height="14" viewBox="0 0 12 14"><path d="M8 2 3 7l5 5" fill="none" stroke="#777" stroke-width="1.5"/></svg></div>
  <div class="arrow" style="left:1090px;top:356px"><svg width="12" height="14" viewBox="0 0 12 14"><path d="M4 2l5 5-5 5" fill="none" stroke="#777" stroke-width="1.5"/></svg></div>

  <article class="service-card" style="left:150px">
    <svg width="64" height="64" viewBox="0 0 64 64" fill="none" stroke="#222" stroke-width="2"><circle cx="26" cy="32" r="18"/><circle cx="26" cy="32" r="24" stroke-dasharray="6 6"/><rect x="16" y="22" width="20" height="6" stroke="var(--red)"/><rect x="16" y="30" width="20" height="6" stroke="var(--red)"/><rect x="16" y="38" width="20" height="6" stroke="var(--red)"/><path d="M44 20h10M44 32h14M44 44h10" stroke="var(--red)"/><circle cx="56" cy="20" r="2" stroke="var(--red)"/><circle cx="60" cy="32" r="2" stroke="var(--red)"/><circle cx="56" cy="44" r="2" stroke="var(--red)"/></svg>
    <h3>IT SUPPORT</h3>
    <p>Avoid expensive shutdowns, security issues, and maintenance problems with proactive attention to your technology systems</p>
    <a class="btn btn-sm" href="#">READ MORE</a>
  </article>
  <article class="service-card featured" style="left:379px">
    <svg width="64" height="64" viewBox="0 0 64 64" fill="none" stroke="#222" stroke-width="2"><path d="M18 28a10 10 0 0 1 2-19 14 14 0 0 1 26 4 8 8 0 0 1 0 15z" stroke="var(--red)"/><path d="M32 28v10M14 38h36M14 38v6M32 38v6M50 38v6"/><rect x="6" y="44" width="16" height="10"/><rect x="24" y="44" width="16" height="10"/><rect x="42" y="44" width="16" height="10"/><path d="M10 58h8M28 58h8M46 58h8"/></svg>
    <h3>CLOUD SERVICES</h3>
    <p>Move away from the restrictions of on-premise architecture and devices. Cloud solutions have reshaped our productivity and how we access</p>
    <a class="btn btn-sm" href="#">READ MORE</a>
  </article>
  <article class="service-card" style="left:608px">
    <svg width="64" height="64" viewBox="0 0 64 64" fill="none" stroke="#222" stroke-width="2"><rect x="4" y="10" width="14" height="46" rx="4"/><rect x="18" y="16" width="40" height="40" rx="3"/><rect x="24" y="22" width="28" height="8" stroke="var(--red)"/><g stroke="var(--red)"><circle cx="28" cy="38" r="2"/><circle cx="38" cy="38" r="2"/><circle cx="48" cy="38" r="2"/><circle cx="28" cy="48" r="2"/><circle cx="38" cy="48" r="2"/><circle cx="48" cy="48" r="2"/></g></svg>
    <h3>PHONE SYSTEMS</h3>
    <p>Move away from the restrictions of on-premise architecture and devices. Cloud solutions have reshaped our productivity and how we access</p>
    <a class="btn btn-sm" href="#">READ MORE</a>
  </article>
  <article class="service-card" style="left:836px">
    <svg width="64" height="64" viewBox="0 0 64 64" fill="none" stroke="#222" stroke-width="2"><circle cx="32" cy="32" r="18"/><rect x="25" y="30" width="14" height="11" stroke="var(--red)"/><path d="M28 30v-4a4 4 0 0 1 8 0v4" stroke="var(--red)"/><path d="M32 6v8M32 50v8M6 32h8M50 32h8M14 14l6 6M44 44l6 6M50 14l-6 6M14 50l6-6"/><circle cx="32" cy="5" r="2"/><circle cx="5" cy="32" r="2"/><circle cx="59" cy="32" r="2"/><circle cx="32" cy="59" r="2"/></svg>
    <h3>CYBER SECURITY</h3>
    <p>Whether you need a risk assessment, security software, policy development, or anything cybersecurity-related, we have you covered!</p>
    <a class="btn btn-sm" href="#">READ MORE</a>
  </article>
</section>

<section class="welcome">
  <svg class="abs" style="left:620px;top:0" width="580" height="407" viewBox="0 0 580 407">
    <defs><linearGradient id="dc" x1="0" y1="0" x2="1" y2="1"><stop offset="0" stop-color="#2a3a55"/><stop offset=".5" stop-color="#18243a"/><stop offset="1" stop-color="#0e1522"/></linearGradient></defs>
    <polygon points="22,0 68,0 110,220 64,226" fill="var(--red)"/>
    <polygon points="16,183 60,183 108,407 62,407" fill="var(--red-dark)"/>
    <polygon points="68,0 580,0 580,407 108,407 60,183 110,220" fill="url(#dc)" role="img" aria-label="IT engineer holding a laptop in a server room"/>
  </svg>
  <h2 class="abs pill-title welcome-pill">WELCOME TO</h2>
  <div class="abs logo-word welcome-name">harbourline</div>
  <p>Founded in 1997 in Sydney, Harbourline IT began as a dedicated IT managed services provider, delivering reliable technology solutions to local businesses. Since then, our expertise, services, and support have evolved significantly, transforming us into a leading End-to-End IT Solutions provider for Small &amp; Medium Businesses.</p>
  <a class="abs btn btn-sm" style="left:358px;top:346px" href="#">READ MORE</a>
</section>

<section>
  <div class="ghost" style="top:1716px">TESTIMONIALS</div>
  <h2 class="pill-title" style="left:467px;top:1828px;width:266px">TESTIMONIALS</h2>
  <div class="arrow" style="left:71px;top:2030px"><svg width="12" height="14" viewBox="0 0 12 14"><path d="M8 2 3 7l5 5" fill="none" stroke="#777" stroke-width="1.5"/></svg></div>
  <div class="arrow" style="left:1091px;top:2030px"><svg width="12" height="14" viewBox="0 0 12 14"><path d="M4 2l5 5-5 5" fill="none" stroke="#777" stroke-width="1.5"/></svg></div>

  <blockquote class="testimonial" style="left:156px">
    <p>For over 12 years Harbourline has been supporting and consulting with us on best practice for our business IT environment. They consistently provide us with cutting-edge solutions and take the time to explain why each decision is made. We place great trust in Harbourline and it gives us the peace of mind to continue operating our business as normal.</p>
  </blockquote>
  <div class="quote-mark" style="left:148px;top:1916px">“</div>
  <svg class="abs" style="left:205px;top:2148px" width="24" height="14"><path d="M0 1 12 13 24 1" fill="#fff" stroke="#cfcfcf" stroke-width="1.5"/></svg>
  <div class="author" style="left:239px"><div class="client-badge"><i></i>Larkspur Property</div><div><b>Carla Denholm</b><span>Operations Manager</span></div></div>

  <blockquote class="testimonial" style="left:627px">
    <p>The guys at Harbourline IT were fantastic to deal with when helping us build our website from scratch. They helped us with everything from the marketing strategy, the colour scheme, the design &amp; the logo. We are very impressed with the outcome and highly recommend them.</p>
  </blockquote>
  <div class="quote-mark" style="left:620px;top:1916px">“</div>
  <svg class="abs" style="left:676px;top:2148px" width="24" height="14"><path d="M0 1 12 13 24 1" fill="#fff" stroke="#cfcfcf" stroke-width="1.5"/></svg>
  <div class="author" style="left:708px"><div class="client-badge"><i style="background:var(--red)"></i>Kestrel Tool Depot</div><div><b>Marcus Ellory</b><span>Director</span></div></div>
</section>

<section class="blog">
  <div class="ghost" style="top:46px">LATEST BLOG</div>
  <h2 class="pill-title" style="left:467px;top:146px;width:266px">LATEST BLOG</h2>
  <article class="post" style="left:150px">
    <div class="post-image" role="img" aria-label="Bowls of coloured sweets being sorted by hand" style="background:linear-gradient(160deg,#e6e2dc,#c9bfb4 60%,#b7a89c)"></div>
    <h3>MAILDESK RULES: WHAT THEY ARE AND HOW TO USE THEM EFFECTIVELY</h3>
    <p>Automate Your Inbox and Boost Productivity Managing your inbox can feel like a full-time job, especially when emails keep pouring in.</p>
    <a class="btn btn-sm" href="#">READ MORE</a>
  </article>
  <article class="post" style="left:459px">
    <div class="post-image" role="img" aria-label="City skyline with connected network icons over a world map" style="background:linear-gradient(170deg,#7fb6d6,#3f7fa8 55%,#1f4766)"></div>
    <h3>THE IMPORTANCE OF HIGH-SPEED, STABLE INTERNET FOR SMBS</h3>
    <p>Poor Connectivity Can Really Hurt Your Business’s Digital Lifeline How much does your business depend on the internet?</p>
    <a class="btn btn-sm" href="#">READ MORE</a>
  </article>
  <article class="post" style="left:766px">
    <div class="post-image" role="img" aria-label="Hands typing on a laptop with email envelope icons" style="background:linear-gradient(160deg,#e9e8f4,#c9c8dc 55%,#9f9fc0)"></div>
    <h3>MAILDESK BLUES? HOW TO FIX COMMON EMAIL SENDING &amp; RECEIVING ISSUES</h3>
    <p>How to Fix Sending and Receiving Issues Ever hit “send” only to wonder if your email vanished into the digital void?</p>
    <a class="btn btn-sm" href="#">READ MORE</a>
  </article>
</section>

<div class="footer-rule"></div>
<footer class="footer">
  <div class="abs logo-word footer-name">harbourline</div>
  <h4 style="left:462px;top:58px">OUR SOLUTIONS</h4>
  <ul style="left:462px;top:115px">
    <li>IT Support</li><li>Project Management</li><li>IT Consulting and Training</li><li>Hardware and Software</li><li>IT Cyber Security</li><li>Cloud Solutions</li><li>IT Procurement and Auditing</li><li>Mobile and Web Development</li>
  </ul>
  <h4 style="left:706px;top:58px">MENU</h4>
  <ul style="left:706px;top:115px">
    <li>Home</li><li>About Us</li><li>Services</li><li>Blog</li><li>Contact Us</li>
  </ul>
  <a class="btn btn-footer" style="top:54px" href="#">REQUEST QUOTES</a>
  <a class="btn btn-footer" style="top:117px" href="#">BOOK CONSULTATIONS</a>
  <h4 style="left:844px;top:201px">FOLLOW US</h4>
  <div class="footer-line"></div>
  <p class="copyright">Copyright © 2025 All Rights Reserved</p>
</footer>
<div class="socials" aria-label="Social media links">
  <span aria-label="Social link 1"></span><span aria-label="Social link 2"></span><span aria-label="Social link 3"></span><span aria-label="Social link 4"></span><span aria-label="Social link 5"></span>
</div>

</body>
</html>
```